Professional Baby Bottle Bank Print Design

We need a baby bottle design that is 4.25" wide x 2.28" tall with a maximum of 6 colors (white is counted as a color).

The bottle design needs to be fun but professional. Bottles with cartoon images on it will be rejected immediately.

The bottle design wraps around the bottle. See examples here: https://vel.quin/cat/BabyBottles/HarlowBottles/5

Minimum font size is 10pt.

The bottle design must have the following text on it:
Main Text: Love them both
Paragraph text: Our ministry’s aim is to not only save unborn babies, but to provide love, support, and life-saving resources for vulnerable women in our community. By filling this bottle with cash, checks, and spare coins and returning it on collection day, you are truly saving and changing lives!
Optional text: Thank you!

We are including an example file and a template file. You do NOT have to use the template - but your file has to be the exact size mentioned. If you don't design as well as our sample, please don't waste our time by spamming us with hundreds of designs. We will ban design houses that spam us with designs that are more layouts (and not well designed).

Please note - white is a color. You don't have to do a box - but anything you don't make white will be see-through.

We will take the winners of this contest to a survey with the customers. We may choose two and edit the text of one slightly to be different. We must know the fonts used.

No gradients unless they are half-toned with relatively big sized dots.

Target Market(s)

Church Attendees coming from a Pregnancy Center

Industry/Entity Type

Religious Christian Churches

Requirements
Must have
• Professional, great palette, wording as described.
Nice to have
• Integrated design across the whole space with areas for text (no text all the way across)
Should not have
• Cartoon figures; elements shoved together that don't go together (i.e. - actually design something)

```html
<!DOCTYPE html>
<html lang="en">
<head>
<meta charset="utf-8">
<title>Love Them Both – Baby Bottle Bank Wrap</title>
<link rel="stylesheet" href="https://fonts.googleapis.com/css2?family=Abril+Fatface&family=Fraunces:opsz,wght@9..144,700;9..144,900&display=swap">
<style>
  :root {
    --paper: #ffffff;
    --sky: #b9e1eb;
    --sky-deep: #93cee0;
    --lilac: #9c98c9;
    --blush: #f4abaf;
    --sage-dark: #46534a;
    --sage: #8fa596;
    --peach: #fdeee8;
    --ink: #2e2e2e;
  }
  html, body {
    margin: 0;
    padding: 0;
    width: 1200px;
    height: 644px;
    overflow: hidden;
    background: var(--paper);
  }
  .bottle-wrap {
    position: relative;
    width: 1200px;
    height: 644px;
    overflow: hidden;
    background: var(--paper);
  }
  .backdrop {
    position: absolute;
    inset: 0;
    width: 1200px;
    height: 644px;
  }
  .illustration {
    position: absolute;
    left: 0;
    top: 8px;
    width: 720px;
    height: 600px;
  }
  .headline {
    position: absolute;
    left: 0;
    top: 0;
    margin: 0;
    font-family: "Abril Fatface", Georgia, serif;
    font-weight: 400;
    line-height: 1;
  }
  .headline span {
    position: absolute;
    white-space: nowrap;
    letter-spacing: -1px;
  }
  .headline .word-love { left: 26px; top: 296px; font-size: 128px; color: var(--sage-dark); }
  .headline .word-them { left: 94px; top: 394px; font-size: 128px; color: var(--lilac); }
  .headline .word-both { left: 26px; top: 496px; font-size: 128px; color: var(--blush); }
  .mission {
    position: absolute;
    right: 44px;
    top: 76px;
    width: 520px;
    margin: 0;
    text-align: right;
    font-family: "Fraunces", Georgia, serif;
    font-weight: 700;
    font-size: 26px;
    line-height: 45.5px;
    color: var(--ink);
  }
  .thanks {
    position: absolute;
    right: 44px;
    top: 446px;
    margin: 0;
    font-family: "Fraunces", Georgia, serif;
    font-weight: 900;
    font-size: 54px;
    line-height: 1;
    color: var(--ink);
  }
</style>
</head>
<body>
<main class="bottle-wrap">
  <svg class="backdrop" viewBox="0 0 1200 644" aria-hidden="true">
    <!-- right blush edge -->
    <path fill="var(--blush)" d="M1172,0 L1200,0 L1200,340 C1168,320 1140,280 1138,230 C1136,170 1160,120 1160,60 C1160,30 1166,12 1172,0 Z"/>
    <path fill="var(--blush)" d="M1046,588 C1080,560 1120,540 1160,520 C1180,510 1195,500 1200,495 L1200,644 L1046,644 Z"/>
    <!-- sky band and bubble shape -->
    <path fill="var(--sky)" d="M0,115 L160,113 C240,112 320,80 420,60 C520,48 600,52 680,80 C720,95 700,260 700,360 C700,420 760,430 780,470 C790,500 770,530 720,532 L0,520 Z"/>
    <path fill="var(--sky-deep)" d="M700,370 C760,380 790,430 782,480 C776,515 750,530 720,532 L712,520 C745,510 760,470 745,430 C735,400 715,385 700,380 Z"/>
    <!-- lilac base wave -->
    <path fill="var(--lilac)" d="M0,557 C90,620 200,644 300,640 C460,634 600,560 760,536 C880,522 1000,540 1100,580 C1150,600 1180,620 1200,636 L1200,644 L0,644 Z"/>
  </svg>

  <svg class="illustration" viewBox="0 0 720 600" role="img" aria-label="Illustration of a mother with long dark green hair, eyes closed, tenderly holding her sleeping newborn baby against her face">
    <defs>
      <linearGradient id="illustration-tone" x1="0" y1="0" x2="1" y2="1">
        <stop offset="0" stop-color="var(--sage)"/>
        <stop offset="0.5" stop-color="#c9d3c8"/>
        <stop offset="1" stop-color="var(--peach)"/>
      </linearGradient>
    </defs>
    <path fill="url(#illustration-tone)" d="M0,230 C60,150 150,40 300,10 C420,-8 500,60 520,160 C540,200 560,210 600,250 C640,300 640,420 610,500 C590,560 560,590 520,592 L360,592 C330,560 320,500 300,470 C240,430 160,380 110,320 C80,290 30,280 0,275 Z"/>
  </svg>

  <h1 class="headline" aria-label="Love Them Both">
    <span class="word-love">Love</span>
    <span class="word-them">Them</span>
    <span class="word-both">Both</span>
  </h1>

  <p class="mission">Our ministry’s aim is to not only save unborn babies, but to provide love, support, and life-saving resources for vulnerable women in our community. By filling this bottle with cash, checks, and spare coins and returning it on collection day, you are truly saving and changing lives!</p>

  <p class="thanks">Thank you!</p>
</main>
</body>
</html>
```